Business Card Design

It's an investment advisory service for individuals with all there investment needs. Also financial consulting to businesses and governmental agencies on retirement plans etc. It's personalized not commoditized help. Should show strength, knowledge and money orientation.

Reason: Will be out of town setting up office.

Reason: waiting for the 2/3rds of group to vote

Reason: only half the votes are in, I'm calling and getting verbals, but at this time we are down to 2 designs.

Industry/Entity Type

Investment

Contact Information for Business Card

B. Rel K. Financial Consulting and Wealth Management, Berislav Mike Holcek, 5172 Pasadena Loma Verde, San Diego, CA 94417-6381, Registered Investment Advisor

Requirements
Nice to have
• Something money oriented

```html
<!DOCTYPE html>
<html lang="en">
<head>
<meta charset="utf-8">
<title>B. Rel K. Business Card</title>
<link rel="stylesheet" href="https://fonts.googleapis.com/css2?family=Open+Sans:wght@400;600;700&family=Roboto+Condensed:wght@700&display=swap">
<style>
  :root {
    --page: #ececec;
    --lime: #abcd2a;
    --navy: #14203a;
    --blue: #1a8fd8;
    --ink: #1d2430;
    --ink-soft: #3a4250;
    --coin-dark: #3b3418;
    --coin-gold: #9a8a3c;
  }
  * { box-sizing: border-box; margin: 0; padding: 0; }
  html, body { width: 1200px; height: 1200px; overflow: hidden; }
  body {
    background: var(--page);
    font-family: "Open Sans", sans-serif;
    position: relative;
  }
  .card {
    position: absolute;
    left: 100px; top: 314px;
    width: 1000px; height: 571px;
    background: var(--lime);
    overflow: hidden;
    box-shadow: 0 10px 30px rgba(0,0,0,0.12);
  }
  .brand-band {
    position: absolute;
    left: 150px; top: 80px;
    width: 850px; height: 170px;
    background: var(--navy);
  }
  .savings-art {
    position: absolute;
    left: 150px; top: 10px;
    width: 850px; height: 100px;
    background: linear-gradient(180deg, rgba(171,205,42,0) 0%, var(--coin-gold) 45%, var(--coin-dark) 100%);
    opacity: 0.85;
  }
  .brand-mark {
    position: absolute;
    left: 340px; top: 125px;
    display: flex; align-items: center; gap: 12px;
    font-family: "Roboto Condensed", sans-serif;
    font-weight: 700;
    font-size: 58px;
    color: var(--blue);
    line-height: 1;
  }
  .brand-mark .square {
    width: 40px; height: 40px;
    background: var(--blue);
  }
  .brand-tagline {
    position: absolute;
    left: 610px; top: 150px;
    font-family: "Roboto Condensed", sans-serif;
    font-weight: 700;
    font-size: 34px;
    line-height: 1.1;
    color: var(--lime);
  }
  .person {
    position: absolute;
    left: 60px; top: 280px;
  }
  .person-name {
    font-weight: 700;
    font-size: 30px;
    color: var(--ink);
  }
  .person-title {
    font-weight: 400;
    font-size: 19px;
    color: var(--ink-soft);
    margin-top: 2px;
  }
  .address {
    position: absolute;
    left: 60px; top: 370px;
    font-size: 24px;
    line-height: 1.3;
    color: var(--ink-soft);
  }
  .accent-bar {
    position: absolute;
    left: 30px; top: 380px;
    width: 10px; height: 80px;
    background: var(--navy);
  }
  .contact-divider {
    position: absolute;
    left: 440px; top: 440px;
    width: 2px; height: 80px;
    background: var(--ink-soft);
    opacity: 0.6;
  }
  .contacts {
    position: absolute;
    left: 458px; top: 440px;
    list-style: none;
  }
  .contacts li {
    display: flex; align-items: center; gap: 10px;
    font-size: 21px;
    color: var(--ink);
    height: 27px;
  }
  .contacts svg { width: 20px; height: 20px; flex: none; }
</style>
</head>
<body>
  <div class="card">
    <div class="brand-band"></div>
    <div class="savings-art" role="img" aria-label="Row of coin stacks with green sprouts growing from them"></div>
    <div class="brand-mark"><span class="square"></span>B. Rel K.</div>
    <div class="brand-tagline">Financial Consulting and<br>Wealth Management</div>

    <div class="person">
      <div class="person-name">Berislav Mike Holcek</div>
      <div class="person-title">Registered Investment Advisor</div>
    </div>
    <div class="accent-bar"></div>
    <div class="address">5172 Pasadena Loma Verde<br>San Diego, CA 94417-6381</div>

    <div class="contact-divider"></div>
    <ul class="contacts">
      <li>
        <svg viewBox="0 0 20 20"><circle cx="10" cy="10" r="10" fill="#1d2430"/><rect x="7" y="5" width="6" height="10" rx="1" fill="#abcd2a"/></svg>
        (xxx) xxx-xxxx
      </li>
      <li>
        <svg viewBox="0 0 20 20"><circle cx="10" cy="10" r="10" fill="#1d2430"/><rect x="6" y="6" width="8" height="8" fill="#abcd2a"/></svg>
        xxxxxxxxxx
      </li>
      <li>
        <svg viewBox="0 0 20 20"><circle cx="10" cy="10" r="10" fill="#1d2430"/><rect x="5" y="7" width="10" height="7" fill="#abcd2a"/><path d="M5 7 L10 11 L15 7" stroke="#1d2430" stroke-width="1.2" fill="none"/></svg>
        xxxxxxxx@xxxxxxx.com
      </li>
    </ul>
  </div>
</body>
</html>
```